Redesign of business card for Cedar Ridge Mechanical

We are looking for a new design for our business cards for Cedar Ridge Mechanical. We are a plumbing & HVAC construction company, operating on the West Coast of Canada and USA. Logo attached.
Industry/Entity Type
Construction - Plumbing & HVAC
Contact Information for Business Card
Name, address, phone numbers, email, website address
Look and feel
Each slider illustrates characteristics of the customer's brand and the style your logo design should communicate.

```html
<!DOCTYPE html>
<html lang="en">
<head>
<meta charset="UTF-8">
<title>Cedar Ridge Mechanical – Business Card</title>
<link href="https://fonts.googleapis.com/css2?family=Montserrat:wght@400;500;700&display=swap" rel="stylesheet">
<style>
  :root {
    --canvas-bg: #2a2a2a;
    --card-black: #111111;
    --card-back: #1b1b1b;
    --ink-white: #ffffff;
    --ink-soft: #e8e8e8;
  }
  * { margin: 0; padding: 0; box-sizing: border-box; }
  html, body {
    width: 1200px; height: 963px; overflow: hidden;
    background: var(--canvas-bg);
    font-family: "Montserrat", sans-serif;
  }
  .sheet {
    width: 1200px; height: 963px;
    display: flex; flex-direction: column;
    align-items: center; justify-content: center; gap: 56px;
  }
  .card {
    position: relative;
    width: 700px; height: 400px;
    border-radius: 24px;
    overflow: hidden;
    color: var(--ink-white);
  }
  .card--front { background: var(--card-black); }
  .card--back {
    background: var(--card-back);
    display: flex; align-items: center; justify-content: center;
  }
  .card__frame { position: absolute; inset: 0; }
  .identity {
    position: absolute; right: 365px; top: 160px;
    text-align: right;
  }
  .identity__name {
    font-weight: 700; font-size: 23px; letter-spacing: 0.5px;
    text-transform: uppercase; white-space: nowrap;
  }
  .identity__role {
    font-weight: 400; font-size: 16px; color: var(--ink-soft);
    margin-top: 2px;
  }
  .divider {
    position: absolute; left: 350px; top: 150px;
    width: 1.5px; height: 96px; background: var(--ink-white);
  }
  .contacts {
    position: absolute; left: 366px; top: 152px;
    list-style: none;
  }
  .contacts__item {
    display: flex; align-items: center; gap: 8px;
    font-size: 17px; font-weight: 400; line-height: 30px;
  }
  .contacts__icon { width: 15px; height: 15px; flex: none; }
  .address {
    position: absolute; left: 160px; top: 368px;
    width: 290px; text-align: center;
    font-size: 16px; font-weight: 400; line-height: 20px;
    white-space: nowrap;
  }
  .brand {
    display: flex; align-items: center; gap: 18px;
  }
  .brand__mark {
    width: 34px; height: 34px;
    border: 4px solid var(--ink-white); border-radius: 4px;
  }
  .brand__name {
    font-weight: 700; font-size: 36px; letter-spacing: 1px;
    text-transform: uppercase; color: var(--ink-white);
  }
</style>
</head>
<body>
<main class="sheet">
  <section class="card card--front" aria-label="Business card front">
    <svg class="card__frame" width="700" height="400" viewBox="0 0 700 400" fill="none" stroke="#ffffff" stroke-width="3" stroke-linecap="round">
      <path d="M52 22 H40 A18 18 0 0 0 22 40 V360 A18 18 0 0 0 40 378 H150"/>
      <path d="M90 22 H660 A18 18 0 0 1 678 40 V360 A18 18 0 0 1 660 378 H460"/>
    </svg>

    <div class="identity">
      <p class="identity__name">Jonathan Smith</p>
      <p class="identity__role">Manager</p>
    </div>
    <div class="divider"></div>

    <ul class="contacts">
      <li class="contacts__item">
        <svg class="contacts__icon" viewBox="0 0 16 16" fill="#fff"><path d="M3.5 1.5l2.5 0 1 3.5-1.8 1.2a8 8 0 0 0 4.6 4.6L11 9l3.5 1v2.5A2 2 0 0 1 12.5 14.5 11 11 0 0 1 1.5 3.5a2 2 0 0 1 2-2z"/></svg>
        123-456-2100
      </li>
      <li class="contacts__item">
        <svg class="contacts__icon" viewBox="0 0 16 16" fill="none" stroke="#fff" stroke-width="1.6"><rect x="1.5" y="3.5" width="13" height="9" rx="1"/><path d="M1.5 4l6.5 5 6.5-5"/></svg>
        youremail@mailbox.com
      </li>
      <li class="contacts__item">
        <svg class="contacts__icon" viewBox="0 0 16 16" fill="none" stroke="#fff" stroke-width="1.4"><circle cx="8" cy="8" r="6.5"/><path d="M1.5 8h13M8 1.5c2 2 2 11 0 13M8 1.5c-2 2-2 11 0 13"/></svg>
        www.yourwebsite.com
      </li>
    </ul>

    <p class="address">Your address, city, state, ZIP 0000</p>
  </section>

  <section class="card card--back" aria-label="Business card back">
    <div class="brand">
      <span class="brand__mark"></span>
      <span class="brand__name">Cedar Ridge Mechanical</span>
    </div>
  </section>
</main>
</body>
</html>
```